Business Card Design For A Renovation Contractor Company

We need a business card for a new company based in Singapore, our company name is "RB Tolvane". We are a renovation contractor that builds designs into reality. We build more of F&B restaurants, retail stores and commercial offices. We work very closely with designers. The final design should communicate to our client that we are a company that you can trust, that will plan and complete your project without giving you a headache. I like my client to remember my company as "RB". The beauty of SIMPLE is important.

Industry/Entity Type

Contractor

Requirements
Nice to have
• Black or Red base

```html
<!DOCTYPE html>
<html lang="en">
<head>
<meta charset="utf-8">
<title>RB Tolvane – Business Card</title>
<link rel="stylesheet" href="https://fonts.googleapis.com/css2?family=Questrial&family=Open+Sans:wght@400;700&display=swap">
<style>
  :root {
    --ink: #1a1a1a;
    --red: #d7262e;
    --white: #ffffff;
    --black: #161616;
    --grey: #8a8a8a;
    --stage: #ecebe8;
  }
  * { margin: 0; padding: 0; box-sizing: border-box; }
  html, body { width: 1200px; height: 720px; overflow: hidden; background: var(--stage); }
  .canvas { position: relative; width: 1200px; height: 720px; }

  .card {
    position: absolute; top: 206px; width: 540px; height: 309px;
    background: var(--white); overflow: hidden;
    box-shadow: 0 2px 10px rgba(0,0,0,.12);
  }
  .card--back { left: 40px; display: flex; }
  .card--front { left: 620px; display: flex; flex-direction: column; align-items: center; justify-content: center; }

  .brand { display: flex; flex-direction: column; align-items: center; }
  .brand__mark {
    width: 62px; height: 62px; border-radius: 50%;
    border: 7px solid var(--red); margin-bottom: 12px;
  }
  .brand__name {
    font-family: "Questrial", sans-serif; font-size: 40px; line-height: 1;
    color: var(--ink); letter-spacing: .5px; padding: 0 6px 4px;
    border-bottom: 1.5px solid var(--grey);
  }
  .brand__tagline {
    font-family: "Questrial", sans-serif; font-size: 15.5px; color: var(--ink);
    margin-top: 3px; letter-spacing: .3px;
  }

  .card__brand-side {
    width: 53%; display: flex; align-items: center; justify-content: center;
    border-right: 2px solid var(--red);
  }
  .card__brand-side .brand__name { font-size: 34px; }
  .card__brand-side .brand__tagline { font-size: 13.5px; }
  .card__brand-side .brand__mark { width: 54px; height: 54px; border-width: 6px; }

  .card__contact-side {
    position: relative; flex: 1; background: var(--black); color: var(--white);
    padding: 34px 20px 0 24px; font-family: "Open Sans", sans-serif;
    border-left: 5px solid var(--white);
  }
  .contact__name { font-weight: 700; font-size: 17px; line-height: 1.2; }
  .contact__title { color: var(--red); font-size: 12px; margin-bottom: 10px; }
  .contact__list { list-style: none; font-size: 13px; line-height: 1.65; }
  .contact__list li { display: flex; align-items: center; gap: 8px; }
  .contact__list svg { width: 11px; height: 11px; flex: none; }
  .contact__address { font-size: 13px; line-height: 1.35; margin-top: 12px; }

  .website {
    font-family: "Open Sans", sans-serif; font-size: 17px; letter-spacing: 3px;
    color: var(--ink); margin-top: 34px;
  }
  .website__accent { color: var(--red); font-weight: 700; }
</style>
</head>
<body>
<main class="canvas">

  <section class="card card--back" aria-label="Card back">
    <div class="card__brand-side">
      <div class="brand">
        <span class="brand__mark" aria-hidden="true"></span>
        <span class="brand__name">RB Tolvane</span>
        <span class="brand__tagline">turning plans into places</span>
      </div>
    </div>
    <div class="card__contact-side">
      <p class="contact__name">Your Name</p>
      <p class="contact__title">Title</p>
      <ul class="contact__list">
        <li><svg viewBox="0 0 12 12" aria-hidden="true"><path d="M2 1h3l1 3-1.5 1a6 6 0 0 0 2.5 2.5L8 6l3 1v3c-5 1-10-4-9-9z" fill="#d7262e"/></svg>123-456-0789</li>
        <li><svg viewBox="0 0 12 12" aria-hidden="true"><rect x="3" y="0.5" width="6" height="11" rx="1.2" fill="#d7262e"/><rect x="4" y="2" width="4" height="6" fill="#161616"/></svg>123-456-0789</li>
        <li><svg viewBox="0 0 12 12" aria-hidden="true"><rect x="0.5" y="2" width="11" height="8" rx="1" fill="#d7262e"/><path d="M1 2.5l5 4 5-4" stroke="#161616" stroke-width="1.2" fill="none"/></svg>info@rbtolvane.com</li>
        <li><svg viewBox="0 0 12 12" aria-hidden="true"><circle cx="6" cy="6" r="5" fill="none" stroke="#d7262e" stroke-width="1.4"/><path d="M1 6h10M6 1c-2.5 3-2.5 7 0 10M6 1c2.5 3 2.5 7 0 10" stroke="#d7262e" fill="none"/></svg>www.rbtolvane.com</li>
      </ul>
      <p class="contact__address">Street Name, City Name<br>State Zip Code</p>
    </div>
  </section>

  <section class="card card--front" aria-label="Card front">
    <div class="brand">
      <span class="brand__mark" aria-hidden="true"></span>
      <span class="brand__name">RB Tolvane</span>
      <span class="brand__tagline">turning plans into places</span>
    </div>
    <p class="website">www.rb<span class="website__accent">tolvane</span>.com</p>
  </section>

</main>
</body>
</html>
```